Flat bootstrap design for existing site

I'm looking for a modern flat design based around an existing logo. This has to be a custom design (no external templates), and implemented into a bootstrap framework.

The logo is attached as 2 versions - choose whichever you want, that flows better with whatever design you choose.

Added screenshots of the existing site (currently using the default bootstrap layouts). Please make your designs around those pages in the screenshots (i.e. the homepage only has the postal code input and the header). The active page has 3 screenshots, because I wanted to illustrate the other states that would be visible (in the table rows).

This is a moving/junk removal website, just for some context.

Here's some example websites (flat designs) that I like, just to give you an idea of what I'm after.

https://www.plimvora.com/
https://dacklow.com/
https://trevanu.com/
https://quobrintal.com/en/

Coding

Coded - Design and coding required

Number of Pages Required

5+ page

Colors

Designer to choose colors to be used in the design.

Requirements
Must have
• It must be a modern/simple flat design, that is built around the existing logo (attached).
• It has to be implemented using bootstrap.

```html
<!DOCTYPE html>
<html lang="en">
<head>
<meta charset="utf-8">
<title>HAULVEX – Booking details</title>
<link href="https://fonts.googleapis.com/css2?family=Mulish:wght@400;600;700;800&display=swap" rel="stylesheet">
<style>
  :root{
    --sky:#3ec4f2;
    --sky-deep:#0aaaf0;
    --header:#05b0f0;
    --title:#2b8fd4;
    --accent:#4ac6f0;
    --ink:#333c44;
    --muted:#555d63;
    --line:#e3e6e8;
    --field-border:#c9cdd0;
    --row:#f7f7f7;
    --pill:#6f6f6f;
    --white:#ffffff;
  }
  *{box-sizing:border-box;margin:0;padding:0}
  html,body{width:1200px;height:1194px;overflow:hidden}
  body{
    position:relative;
    font-family:"Mulish",Arial,sans-serif;
    color:var(--ink);
    background:linear-gradient(135deg,#52cdf5 0%,var(--sky) 40%,#2fbaf0 70%,#4fcaf4 100%);
  }
  .site-header{
    position:absolute;left:0;top:0;width:1200px;height:108px;
    background:linear-gradient(120deg,var(--header),#12b6f2 50%,#00a8ee);
  }
  .brand{
    position:absolute;left:86px;top:30px;display:flex;align-items:center;gap:10px;
    color:var(--white);font-weight:800;font-size:40px;letter-spacing:1px;
  }
  .brand-dot{width:22px;height:22px;border-radius:50%;background:var(--white)}
  .main-nav{position:absolute;top:40px;left:0;width:100%;font-size:16px;color:var(--white)}
  .main-nav span{position:absolute;white-space:nowrap}
  .caret{display:inline-block;margin-left:5px;border-left:5px solid transparent;border-right:5px solid transparent;border-top:6px solid var(--white);vertical-align:3px}
  .card{position:absolute;background:var(--white);border-radius:6px;box-shadow:0 6px 18px rgba(0,80,130,.12)}
  .card-title{position:absolute;left:0;width:100%;text-align:center;color:var(--title);font-size:30px;font-weight:400;letter-spacing:.3px}
  .rule{position:absolute;height:1px;background:var(--line)}
  .field-label{position:absolute;font-size:18px;font-weight:600;color:var(--ink)}
  .field{
    position:absolute;height:49px;border:1px solid var(--field-border);border-radius:25px;
    box-shadow:0 2px 3px rgba(0,0,0,.12);font-size:15.5px;color:var(--muted);
    display:flex;align-items:center;padding:0 20px;
  }
  .field svg{position:absolute;right:20px;top:50%;transform:translateY(-50%)}
  .btn-update{
    position:absolute;left:427px;top:330px;width:167px;height:53px;border-radius:27px;
    background:var(--accent);color:var(--white);font-size:21px;display:flex;align-items:center;justify-content:center;
    box-shadow:0 4px 8px rgba(0,0,0,.18);
  }
  .notice{position:absolute;left:0;top:104px;width:100%;text-align:center;color:var(--accent);font-size:16.5px}
  .drivers{position:absolute;left:83px;top:159px;width:867px;height:311px;border:1px solid #b9bcbe;background:var(--row)}
  .row{position:absolute;left:0;width:100%;border-bottom:1px solid #dadcde;font-size:14px;color:var(--ink)}
  .row:last-child{border-bottom:none}
  .row.head{font-size:16px}
  .cell{position:absolute;top:50%;transform:translateY(-50%);white-space:nowrap}
  .pill{
    position:absolute;left:727px;top:50%;transform:translateY(-50%);width:102px;height:26px;border-radius:13px;
    background:var(--pill);color:var(--white);font-size:14px;display:flex;align-items:center;justify-content:center;
    box-shadow:0 2px 3px rgba(0,0,0,.25);
  }
</style>
</head>
<body>
  <header class="site-header">
    <div class="brand"><span class="brand-dot"></span>HAULVEX</div>
    <nav class="main-nav">
      <span style="left:485px">BOOK</span>
      <span style="left:583px">HOW IT WORKS</span>
      <span style="left:757px">BECOME A DRIVER</span>
      <span style="left:952px">nina@plovtec.com<i class="caret"></i></span>
    </nav>
  </header>

  <section class="card booking" style="left:89px;top:155px;width:1023px;height:424px">
    <h1 class="card-title" style="top:28px">BOOKING DETAILS</h1>
    <div class="rule" style="left:81px;top:85px;width:867px"></div>
    <label class="field-label" style="left:81px;top:122px">Package selected:</label>
    <div class="field" style="left:79px;top:153px;width:411px">Package 1
      <svg width="11" height="16" viewBox="0 0 11 16"><path d="M5.5 0 11 6H0z M5.5 16 0 10h11z" fill="#555"/></svg>
    </div>
    <label class="field-label" style="left:536px;top:122px">Pick-up time selected:</label>
    <div class="field" style="left:535px;top:153px;width:411px">July18 at 4.13 am
      <svg width="17" height="17" viewBox="0 0 17 17" fill="none" stroke="#555" stroke-width="1.4"><rect x="1" y="2.5" width="15" height="13.5"/><path d="M1 6.5h15M5 0.5v4M12 0.5v4M5 6.5v9.5M8.5 6.5v9.5M12 6.5v9.5M1 10h15M1 13h15"/></svg>
    </div>
    <label class="field-label" style="left:81px;top:222px">Description:</label>
    <div class="field" style="left:79px;top:255px;width:867px">1 large stove</div>
    <div class="btn-update">UPDATE</div>
  </section>

  <section class="card drivers-card" style="left:87px;top:606px;width:1023px;height:518px">
    <h2 class="card-title" style="top:28px">DRIVERS IN YOUR AREA</h2>
    <div class="rule" style="left:81px;top:82px;width:867px"></div>
    <p class="notice">Please stay on this pade and be patient, while we contact drivers and find you one ASP.</p>
    <div class="drivers">
      <div class="row head" style="top:0;height:54px">
        <span class="cell" style="left:24px">Name</span>
        <span class="cell" style="left:168px">Distance(km)</span>
        <span class="cell" style="left:355px">Agreed pick-up time</span>
        <span class="pill" style="top:24px">Pending</span>
      </div>
      <div class="row" style="top:54px;height:62px">
        <span class="cell" style="left:24px">Dale Marsh</span>
        <span class="cell" style="left:168px">4.00km awry</span>
        <span class="cell" style="left:355px">July18 at 4.13 am</span>
        <span class="pill">Pending</span>
      </div>
      <div class="row" style="top:116px;height:60px">
        <span class="cell" style="left:24px">Owen brisk</span>
        <span class="cell" style="left:170px">5.7km away</span>
        <span class="cell" style="left:408px">_</span>
        <span class="pill">Pending</span>
      </div>
      <div class="row" style="top:176px;height:66px">
        <span class="cell" style="left:24px">Calum Ferro</span>
        <span class="cell" style="left:167px">11.13km away</span>
        <span class="cell" style="left:408px">_</span>
        <span class="pill">Pending</span>
      </div>
      <div class="row" style="top:242px;height:69px">
        <span class="cell" style="left:24px">Reid Albany</span>
        <span class="cell" style="left:164px">11.91km away</span>
        <span class="cell" style="left:408px">_</span>
        <span class="pill">Pending</span>
      </div>
    </div>
  </section>
</body>
</html>
```